Landscape design build company door flyer

I would like this flyer to convey a high-level of professionalism for a company that is excellent with communication with their clients as well as a company that does incredible installations

Went on vacation/holiday

```html
<!DOCTYPE html>
<html lang="en">
<head>
<meta charset="utf-8">
<title>Cedar Ridge Builders – Outdoor Living Flyer</title>
<link href="https://fonts.googleapis.com/css2?family=Poppins:wght@400;500;600;700;800;900&display=swap" rel="stylesheet">
<style>
  :root {
    --navy: #0c2a41;
    --heading: #102d46;
    --orange: #f2700c;
    --paper: #e6e6e6;
    --panel: #e9e9e9;
    --white: #ffffff;
    --text: #1d1d1d;
    --stage: #ececec;
  }
  * { box-sizing: border-box; margin: 0; padding: 0; }
  html, body {
    width: 1200px; height: 1029px; overflow: hidden;
    background: var(--stage);
    font-family: "Poppins", sans-serif;
  }
  .flyer {
    position: absolute; left: 211px; top: 14px;
    width: 778px; height: 1000px;
    background: var(--paper);
    overflow: hidden;
    box-shadow: 0 10px 30px rgba(0,0,0,.18);
  }
  .hero-photo {
    position: absolute; left: 0; top: 0; width: 778px; height: 543px;
    background:
      linear-gradient(180deg, rgba(20,45,80,0) 55%, rgba(40,70,50,.85) 100%),
      linear-gradient(135deg, #2b4a74 0%, #2e5386 40%, #3a5b7a 65%, #4a6a4e 100%);
  }
  .brand-panel { position: absolute; left: 0; top: 0; }
  .brand {
    position: absolute; left: 0; top: 0; width: 345px; height: 168px;
    display: flex; flex-direction: column; align-items: center; justify-content: center; gap: 10px;
  }
  .brand-dot { width: 46px; height: 46px; border-radius: 50%; background: var(--orange); }
  .brand-name {
    font-weight: 600; font-size: 18px; letter-spacing: .5px; color: var(--orange);
  }
  .headline {
    position: absolute; left: 39px; top: 222px;
    font-weight: 800; font-size: 53px; line-height: 52px; letter-spacing: -1px;
    color: var(--white); text-transform: uppercase;
  }
  .headline .accent { color: var(--orange); }
  .project-photo {
    position: absolute; top: 419px; width: 206px; height: 206px; border-radius: 50%;
    border: 5px solid var(--white);
  }
  .project-photo.pavilion { left: 46px; background: linear-gradient(160deg, #8a6a4a 0%, #5d6b5a 50%, #4d7a3a 100%); }
  .project-photo.deck-house { left: 287px; background: linear-gradient(180deg, #3f5a3a 0%, #b45a2a 55%, #5c9a3c 100%); }
  .project-photo.steps { left: 526px; background: linear-gradient(160deg, #b8b2a6 0%, #8c6a4a 50%, #a89a82 100%); }
  .section-title {
    position: absolute; top: 650px;
    font-weight: 700; font-size: 25px; color: var(--heading); letter-spacing: -.2px;
  }
  .section-title::after {
    content: ""; position: absolute; left: 2px; top: 38px;
    width: 70px; height: 3px; border-radius: 2px; background: var(--orange);
  }
  .about-title { left: 39px; }
  .services-title { left: 459px; }
  .about-text {
    position: absolute; left: 39px; top: 699px; width: 351px;
    font-size: 13.4px; line-height: 15.9px; color: var(--text);
    text-align: justify; hyphens: auto;
  }
  .service-list { position: absolute; left: 459px; top: 699px; list-style: none; }
  .service-list li {
    display: flex; align-items: center; gap: 16px;
    height: 22.5px; font-weight: 500; font-size: 15px; color: var(--heading);
  }
  .service-list svg { width: 13px; height: 13px; flex: none; }
  .footer { position: absolute; left: 0; top: 0; }
  .phone-icon {
    position: absolute; left: 37px; top: 925px; width: 51px; height: 51px;
    background: var(--orange); display: flex; align-items: center; justify-content: center;
  }
  .phone-number {
    position: absolute; left: 99px; top: 919px;
    font-weight: 700; font-size: 41px; line-height: 60px; letter-spacing: -.5px; color: var(--white);
  }
  .contact-line {
    position: absolute; left: 509px; display: flex; align-items: center; gap: 22px;
    font-size: 14.5px; color: var(--white);
  }
  .contact-line svg { width: 16px; height: 16px; flex: none; }
  .contact-line.email { top: 921px; }
  .contact-line.web { top: 946px; }
</style>
</head>
<body>
<main class="flyer">
  <div class="hero-photo" role="img" aria-label="Photo of a finished composite deck with dark railings and wide stairs beside a blue house"></div>

  <svg class="brand-panel" width="778" height="170" viewBox="0 0 778 170">
    <polygon points="0,0 407,0 321,168 0,168" fill="var(--panel)"/>
  </svg>
  <div class="brand">
    <span class="brand-dot"></span>
    <span class="brand-name">CEDAR RIDGE BUILDERS</span>
  </div>

  <h1 class="headline">Let’s create<br>your dream<br><span class="accent">outdoor living space!</span></h1>

  <div class="project-photo pavilion" role="img" aria-label="Photo of a covered outdoor kitchen pavilion with stone bar"></div>
  <div class="project-photo deck-house" role="img" aria-label="Photo of a wraparound deck on a cabin in the woods"></div>
  <div class="project-photo steps" role="img" aria-label="Photo of a new low wood deck with wide stepped edges"></div>

  <h2 class="section-title about-title">ABOUT US</h2>
  <p class="about-text">Discover the endless possibilities for your outdoor space with The Cedar Ridge Builders Team. Our team of skilled artisans is dedicated to turning your outdoor space into a breathtaking oasis that you’ll love coming home to. Whether it’s a cozy patio for intimate gatherings, a sprawling deck to host memorable parties, or a custom paver driveway that adds instant curb appeal, our high-quality craftsmanship ensures stunning results that exceed your expectations.</p>

  <h2 class="section-title services-title">OUR SERVICES</h2>
  <ul class="service-list">
    <li><svg viewBox="0 0 16 16"><circle cx="8" cy="8" r="8" fill="var(--orange)"/><path d="M4.5 8.3l2.3 2.3 4.7-4.9" stroke="#fff" stroke-width="2" fill="none" stroke-linecap="round" stroke-linejoin="round"/></svg>Paver Patios</li>
    <li><svg viewBox="0 0 16 16"><circle cx="8" cy="8" r="8" fill="var(--orange)"/><path d="M4.5 8.3l2.3 2.3 4.7-4.9" stroke="#fff" stroke-width="2" fill="none" stroke-linecap="round" stroke-linejoin="round"/></svg>Paver Driveways</li>
    <li><svg viewBox="0 0 16 16"><circle cx="8" cy="8" r="8" fill="var(--orange)"/><path d="M4.5 8.3l2.3 2.3 4.7-4.9" stroke="#fff" stroke-width="2" fill="none" stroke-linecap="round" stroke-linejoin="round"/></svg>Retaining Walls</li>
    <li><svg viewBox="0 0 16 16"><circle cx="8" cy="8" r="8" fill="var(--orange)"/><path d="M4.5 8.3l2.3 2.3 4.7-4.9" stroke="#fff" stroke-width="2" fill="none" stroke-linecap="round" stroke-linejoin="round"/></svg>Decks &amp; Railings</li>
    <li><svg viewBox="0 0 16 16"><circle cx="8" cy="8" r="8" fill="var(--orange)"/><path d="M4.5 8.3l2.3 2.3 4.7-4.9" stroke="#fff" stroke-width="2" fill="none" stroke-linecap="round" stroke-linejoin="round"/></svg>Pools</li>
    <li><svg viewBox="0 0 16 16"><circle cx="8" cy="8" r="8" fill="var(--orange)"/><path d="M4.5 8.3l2.3 2.3 4.7-4.9" stroke="#fff" stroke-width="2" fill="none" stroke-linecap="round" stroke-linejoin="round"/></svg>Outdoor Lighting</li>
    <li><svg viewBox="0 0 16 16"><circle cx="8" cy="8" r="8" fill="var(--orange)"/><path d="M4.5 8.3l2.3 2.3 4.7-4.9" stroke="#fff" stroke-width="2" fill="none" stroke-linecap="round" stroke-linejoin="round"/></svg>Firepits &amp; Fireplaces</li>
  </ul>

  <svg class="footer" width="778" height="1000" viewBox="0 0 778 1000">
    <rect x="0" y="907" width="778" height="93" fill="var(--navy)"/>
    <polygon points="472,900 778,900 778,1000 432,1000" fill="var(--orange)"/>
  </svg>

  <div class="phone-icon">
    <svg width="28" height="28" viewBox="0 0 24 24"><path fill="#fff" d="M6.6 10.8a15.1 15.1 0 006.6 6.6l2.2-2.2c.3-.3.7-.4 1-.2 1.1.4 2.3.6 3.6.6.6 0 1 .4 1 1V20c0 .6-.4 1-1 1A17 17 0 013 4c0-.6.4-1 1-1h3.5c.6 0 1 .4 1 1 0 1.3.2 2.5.6 3.6.1.3 0 .7-.2 1l-2.3 2.2z"/></svg>
  </div>
  <p class="phone-number">555-014-2290</p>

  <p class="contact-line email">
    <svg viewBox="0 0 16 16"><rect x="0.5" y="2.5" width="15" height="11" rx="1" fill="#fff"/><path d="M1 3.5l7 5 7-5" stroke="var(--orange)" stroke-width="1.4" fill="none"/></svg>
    info@cedarridgebuilders.com
  </p>
  <p class="contact-line web">
    <svg viewBox="0 0 16 16" fill="none" stroke="#fff" stroke-width="1.2"><circle cx="8" cy="8" r="7"/><ellipse cx="8" cy="8" rx="3" ry="7"/><path d="M1 8h14M2.2 4.5h11.6M2.2 11.5h11.6"/></svg>
    www.cedarridgebuilders.com
  </p>
</main>
</body>
</html>
```